Adaptive GS Conversion & Enhancement B2B Site

We are looking to convert our current page to the adaptove Grid System (http://plinq.417.io/) and if there are some general enhancements, we would not complain :-)

We would expect delivery of static html for the following pages:
- home - http://www.bremvilo.com/
- detail - e.g. http://www.bremvilo.com/products/products.html
- help - http://www.bremvilo.com/help/te_reports/customer_approval.html

Our objective is to convert the page to a different system which is then based on the Adapt.js - from mobile.css to 2520.css

Target Market(s)

Business looking for Professional Services Project Management

Requirements
Must have
• Use of http://plinq.417.io/
Should not have
• Flash, or other frameworks (well jQuery is OK if it must be)

```html
<!DOCTYPE html>
<html lang="en">
<head>
<meta charset="utf-8">
<title>Bremvilo Details</title>
<link href="https://fonts.googleapis.com/css2?family=Source+Sans+3:wght@400;600&display=swap" rel="stylesheet">
<style>
:root{
  --orange:#f7a900;
  --orange-dark:#ef9d00;
  --text:#333;
  --muted:#555;
  --link:#666;
  --line:#e6e6e6;
  --panel:#f4f4f4;
  --footer:#f2f2f2;
  --bar:#3b3b3b;
  --white:#fff;
}
*{margin:0;padding:0;box-sizing:border-box}
html,body{width:937px;height:1200px;overflow:hidden}
body{position:relative;background:var(--white);font-family:"Source Sans 3",Arial,sans-serif;color:var(--text)}
.header{position:absolute;left:0;top:0;width:937px;height:112px;background:linear-gradient(#f3f3f3,#fafafa 30%,#fff)}
.header-top{position:absolute;left:0;top:0;width:937px;height:5px;background:#e8e8e8}
.search-tab{position:absolute;left:650px;top:5px;width:217px;height:31px;background:#e9e9e9;clip-path:polygon(0 0,100% 0,94% 100%,5% 100%)}
.search-box{position:absolute;left:664px;top:9px;width:184px;height:20px;background:var(--white);border-radius:10px;font-size:10px;color:#999;padding:4px 12px}
.search-box svg{position:absolute;right:10px;top:4px}
.brand{position:absolute;left:39px;top:44px;display:flex;align-items:center;gap:8px;font-size:29px;font-weight:600;color:#222}
.brand-mark{width:22px;height:22px;border-radius:50%;background:#3a7dbf}
.nav{position:absolute;left:316px;top:68px;width:591px;height:43px;background:linear-gradient(var(--orange),var(--orange-dark));border-radius:4px 4px 0 0;display:flex;align-items:center;padding-left:25px}
.nav a{color:var(--white);font-size:13px;text-decoration:none;padding:0 17px;border-left:1px solid rgba(255,255,255,.6);line-height:14px}
.nav a:first-child{border-left:0;padding-left:0}
.sidebar{position:absolute;left:20px;top:125px;width:258px;height:803px;background:var(--panel);border:1px solid #e4e4e4;border-radius:3px;padding:6px}
.sidebar-inner{background:var(--white);border:1px solid #e6e6e6;height:100%;border-radius:2px;padding:28px 0 0 26px}
.help-menu{list-style:none;width:176px}
.help-menu li{height:25.7px;line-height:23px;font-size:11.6px;color:var(--muted);border-bottom:1px solid #f0f0f0;position:relative;padding-left:14px;white-space:nowrap;overflow:hidden}
.help-menu li::before{content:"›";position:absolute;left:2px;top:0;font-size:11px;color:#888}
.help-menu li.sub{padding-left:29px}
.help-menu li.sub::before{left:19px;color:#bbb}
.content{position:absolute;left:297px;top:144px;width:610px}
.content h1{font-size:18px;font-weight:400;color:#222;margin-bottom:5px;letter-spacing:-.2px}
.content p{font-size:11.2px;line-height:16.5px;color:var(--text);margin-bottom:14px}
.content .gap{margin-top:24px}
.content .gap-wide{margin-top:34px}
.content .inset{margin-left:5px;margin-right:-5px}
.points{list-style:none;margin:18px 0 22px 17px}
.points li{font-size:11.2px;line-height:21px;padding-left:22px;position:relative}
.points li::before{content:"";position:absolute;left:0;top:5px;width:12px;height:12px;border-radius:50%;background:#e4e4e4}
.points li::after{content:"";position:absolute;left:5px;top:8.5px;border-left:4px solid #777;border-top:2.5px solid transparent;border-bottom:2.5px solid transparent}
.footer{position:absolute;left:0;top:943px;width:937px;height:216px;background:var(--footer)}
.footer-col{position:absolute;top:30px}
.footer-col h3{font-size:13.5px;font-weight:400;color:#222;margin-bottom:8px}
.footer-col li{list-style:none;font-size:11px;color:var(--muted);line-height:23px}
.social{display:flex;gap:12px;margin:8px 0 11px 1px}
.social span{width:24px;height:24px;background:#666;border-radius:3px}
.social-links{font-size:11px;color:var(--muted)}
.badge-a{position:absolute;left:736px;top:32px;width:137px;height:53px;background:#1a5d92;border:2px solid #dfe7ef;border-radius:3px}
.badge-b{position:absolute;left:738px;top:92px;width:185px;height:55px;background:var(--white)}
.badge-b i{position:absolute;left:34px;bottom:10px;width:134px;height:11px;background:#e8141b}
.bottom-bar{position:absolute;left:0;top:1159px;width:937px;height:41px;background:var(--bar);color:#ddd;font-size:10.5px;padding:14px 0 0 40px}
</style>
</head>
<body>
<header class="header">
  <div class="header-top"></div>
  <div class="search-tab"></div>
  <div class="search-box">Search here..
    <svg width="12" height="12" viewBox="0 0 12 12"><circle cx="5" cy="5" r="3.8" fill="none" stroke="#777" stroke-width="1.5"/><line x1="7.8" y1="7.8" x2="11" y2="11" stroke="#777" stroke-width="1.6"/></svg>
  </div>
  <div class="brand"><span class="brand-mark"></span>Bremvilo</div>
  <nav class="nav">
    <a>Home</a><a>Products</a><a>Services</a><a>Support</a><a>Blog</a><a>About Us</a><a>Contact Us</a>
  </nav>
</header>

<aside class="sidebar">
  <div class="sidebar-inner">
    <ul class="help-menu">
      <li>Bremvilo Cloud Help</li>
      <li class="sub">Welcome</li>
      <li>Opportunity Workbench</li>
      <li>Time Expense Item Workbench</li>
      <li>Workbench Setup</li>
      <li>Using Time &amp; Expense</li>
      <li class="sub">Time &amp; Expense Items</li>
      <li class="sub">Time &amp; Expense Reports</li>
      <li class="sub">Customer Approval</li>
      <li class="sub">Payment Selection</li>
      <li class="sub">Bremvilo Timer</li>
      <li class="sub">Dashboards &amp; Reporting</li>
      <li>Using Cloud Billing</li>
      <li class="sub">Invoices</li>
      <li>Setup: Accounting</li>
      <li class="sub">Financial Organizations</li>
      <li class="sub">Financial Accounts</li>
      <li class="sub">Taxes</li>
      <li>Setup: Time &amp; Expense</li>
      <li>Setup: Billing</li>
      <li class="sub">Document Types</li>
      <li class="sub">Payment Terms</li>
      <li>Installation</li>
      <li class="sub">Remote Sites</li>
      <li class="sub">Email Processing</li>
      <li class="sub">Security &amp; Sharing</li>
      <li class="sub">Report Approval Process</li>
      <li class="sub">Page Layouts</li>
      <li class="sub">Alerts</li>
    </ul>
  </div>
</aside>

<main class="content">
  <h1>BREMVILO Details</h1>
  <p>Lorem ipsum dolor sit amet, consectetuer adipiscing elit. Nam cursus. Morbi ut mi. Nullam enim leo, egestas id, condimentum at, laoreet mattis, massa.</p>
  <p>Sed eleifend nonummy diam. Praesent mauris ante, elementum et, bibendum at, posuere sit amet, nibh. Duis tincidunt lectus quis dui viverra vestibulum. Suspendisse vulputate aliquam dui. Nulla elementum dui ut augue. Aliquam vehicula mi at mauris. Maecenas placerat, nisl at consequat rhoncus, sem nunc gravida justo, quis eleifend arcu velit quis lacus. Morbi magna magna, tincidunt a, mattis non, imperdiet vitae, tellus. Sed odio est, auctor ac, sollicitudin in, consequat vitae, orci. Fusce id felis. Vivamus sollicitudin metus eget eros.</p>
  <p class="gap">Pellentesque habitant morbi tristique senectus et netus et malesuada fames ac turpis egestas. In posuere felis nec tortor. Pellentesque faucibus. Ut accumsan ultricies elit. Maecenas at justo id velit placerat molestie. Donec dictum lectus non odio. Cras a ante vitae enim iaculis aliquam.</p>
  <ul class="points">
    <li>Nunc tempus felis vitae urna.</li>
    <li>Vivamus porttitor neque at volutpat rutrum, purus nisi eleifend libero</li>
    <li>Tempus libero lectus feugiat felis.</li>
    <li>Morbi diam mauris, viverra in, gravida eu, mattis in, ante.</li>
    <li>Morbi eget arcu Morbi porta, libero id ullamcorper nonummy,</li>
  </ul>
  <div class="inset">
    <p>Phasellus felis dolor, scelerisque a, tempus eget, lobortis id, libero. Donec scelerisque leo ac risus. Praesent sit amet est. In dictum, dolor eu dictum porttitor, enim felis viverra mi, eget luctus massa purus quis odio. Etiam nulla massa, pharetra facilisis, volutpat in, imperdiet sit amet, sem.</p>
    <p>Aliquam nec erat at purus cursus interdum. Vestibulum ligula augue, bibendum accumsan, vestibulum ut, commodo a, mi. Morbi ornare gravida elit. Integer congue, augue et malesuada iaculis, ipsum dui aliquet felis, at cursus magna nisl nec elit. Donec iaculis diam a nisi accumsan viverra. Duis sed tellus et tortor vestibulum gravida. Praesent elementum elit at tellus. Curabitur metus ipsum, luctus eu, malesuada ut, tincidunt sed, diam.</p>
    <p>Maecenas aliquet velit vel turpis. Mauris neque metus, malesuada nec, ultricies sit amet, porttitor mattis, enim. In massa libero, interdum nec, interdum vel, blandit sed, nulla. In ullamcorper, est eget tempor cursus, neque mi consectetuer mi, a ultricies massa est sed nisl. Class aptent taciti sociosqu ad litora torquent per conubia nostra, per inceptos hymenaeos. Proin nulla arcu, nonummy luctus, dictum eget, fermentum et, lorem. Nunc porta convallis pede.</p>
    <p class="gap-wide">Mauris vel lacus vitae felis vestibulum volutpat. Etiam est nunc, venenatis in, tristique eu, imperdiet ac, nisl. Cum sociis natoque penatibus et magnis dis parturient montes, nascetur ridiculus mus. In iaculis facilisis massa.</p>
    <p style="margin-top:-8px">Etiam eu urna. Sed porta. Suspendisse quam leo, molestie sed, luctus quis, feugiat in, pede. Fusce tellus. Sed metus augue, convallis et, vehicula ut, pulvinar eu, ante. Integer orci tellus, tristique vitae, consequat nec, porta vel, lectus. Nulla sit amet diam.</p>
  </div>
</main>

<footer class="footer">
  <div class="footer-col" style="left:39px">
    <h3>Company</h3>
    <ul><li>About Company</li><li>What We Do</li><li>Why We Are</li><li>Recent Blog</li><li>Services Offerd</li></ul>
  </div>
  <div class="footer-col" style="left:184px">
    <h3>Support</h3>
    <ul><li>Help</li><li>FAQ</li><li>Term of Use</li><li>Support</li><li>Contact Us</li></ul>
  </div>
  <div class="footer-col" style="left:314px">
    <h3>Contact Information</h3>
    <ul><li>Phone:+1 (555) 318-4420</li><li>418 Harbor Crest Lane,</li><li>Suite 210-44</li><li>Maple Point, CA 90000</li></ul>
  </div>
  <div class="footer-col" style="left:512px">
    <h3>Get In Touch</h3>
    <div class="social"><span></span><span></span><span></span><span></span></div>
    <div class="social-links">Pagebook / Chirper / Vidstream / RSS</div>
  </div>
  <div class="badge-a" role="img" aria-label="Accreditation badge"></div>
  <div class="badge-b" role="img" aria-label="Partner program badge"><i></i></div>
</footer>
<div class="bottom-bar">© 2012 Company Name.&nbsp; All right resreved</div>
</body>
</html>
```